Flyer for Tallow Brisko - Design Agency

We need a 4-page square flyer measuring 14.8x14.8cm per page, to fold out, for a design agency targeting small businesses.
The design should be very modern. There shouldn't be too much content visible.
The background should be black. The color of the logo (attached) can also be used. The content is also attached and divided per page. We are open to alternative suggestions regarding the division.

```html
<!DOCTYPE html>
<html lang="de">
<head>
<meta charset="utf-8">
<title>Tallow Brisko – Faltflyer</title>
<link href="https://fonts.googleapis.com/css2?family=Gloock&family=Poppins:wght@300;400;500;600;700&display=swap" rel="stylesheet">
<style>
  :root{
    --stage:#eef1f1;
    --ink:#0a0710;
    --violet:#5a1a86;
    --magenta:#cf4cf2;
    --cyan:#93ebe6;
    --cyan-text:#63dde0;
    --pink:#ff3f6f;
    --deep:#3d2a78;
    --white:#ffffff;
    --soft:#d9d3e6;
    --sans:'Poppins', sans-serif;
    --display:'Gloock', serif;
  }
  *{margin:0;padding:0;box-sizing:border-box}
  html,body{width:1200px;height:2165px;overflow:hidden;background:var(--stage);font-family:var(--sans);color:var(--white)}
  .spread{position:absolute;left:50px;width:1100px;height:555px;overflow:hidden;box-shadow:0 14px 30px rgba(0,0,0,.28)}
  .spread--outside{top:487px;background:
      radial-gradient(ellipse 420px 260px at 820px 40px, rgba(130,40,170,.75), transparent 70%),
      radial-gradient(ellipse 360px 220px at 560px 380px, rgba(40,30,140,.55), transparent 70%),
      var(--ink)}
  .spread--inside{top:1122px;background:
      radial-gradient(ellipse 300px 200px at 200px 0px, rgba(110,30,150,.55), transparent 70%),
      radial-gradient(ellipse 520px 260px at 900px 330px, rgba(140,40,170,.8), transparent 70%),
      radial-gradient(ellipse 360px 200px at 350px 420px, rgba(40,30,150,.55), transparent 70%),
      var(--ink)}
  .wave{position:absolute;left:0;top:0;width:1100px;height:555px}
  .abs{position:absolute}
  .art{position:absolute;border-radius:14px}
  .art--line{background:linear-gradient(135deg, rgba(70,90,200,.22), rgba(140,60,200,.12))}
  .art--line-cyan{background:linear-gradient(135deg, rgba(90,160,200,.25), rgba(80,110,190,.12))}
  .art--hero{background:radial-gradient(ellipse at 55% 45%, #8a3ff0 0%, #4b2bb0 45%, rgba(20,10,40,0) 75%)}
  .art--desk{background:radial-gradient(ellipse at 50% 55%, #9a6bf0 0%, #c85a9a 30%, #3a2a9a 55%, rgba(20,10,40,0) 78%)}

  .brand-light{font-weight:300;font-size:34px;line-height:34px}
  .brand-bold{font-weight:700;font-size:34px;line-height:34px;color:var(--magenta)}
  .tagline{font-size:17px;letter-spacing:.32em;font-weight:400}
  .subline{font-size:13px;font-weight:600;color:var(--cyan-text)}
  .contact-pill{left:0;top:322px;width:222px;height:24px;background:var(--deep);border-radius:0 12px 12px 0;font-size:12.5px;line-height:24px;padding-left:34px}
  .offer-title{font-family:var(--display);font-size:29px;line-height:27px;color:var(--deep)}
  .contact-list{list-style:none;font-size:11px;line-height:16px;color:var(--deep);font-weight:500}
  .contact-list li{display:flex;align-items:flex-start;gap:7px}
  .contact-list svg{flex:none;margin-top:3px}
  .url{font-size:14.5px;font-weight:500;letter-spacing:.08em;color:var(--deep)}
  .url b{font-weight:700}
  .wordmark{font-weight:600;font-size:23px;line-height:24px}
  .wordmark--deep{color:var(--deep)}
  .wordmark--cyan{color:var(--cyan-text)}
  .owner-label{font-size:13px;letter-spacing:.3em;color:var(--deep);font-weight:500}
  .owner-names{font-size:16px;line-height:18px;font-weight:700;color:var(--violet)}
  .hero-kicker{font-size:22px;line-height:22px;font-weight:300}
  .hero-kicker b{font-weight:700;color:var(--cyan-text)}
  .hero-title{font-family:var(--display);font-size:58px;line-height:52px}

  .motto{font-size:16px;font-weight:700;letter-spacing:.12em}
  .motto span{color:var(--magenta);margin:0 6px;font-weight:400}
  .brand2-bold{font-weight:700;font-size:28px;line-height:27px;color:var(--magenta)}
  .brand2-light{font-weight:300;font-size:28px;line-height:27px}
  .rule-v{width:2px;background:var(--pink)}
  .intro{font-size:13px;line-height:15px}
  .grafik-pill{left:-2px;top:155px;width:482px;height:74px;border:1px solid var(--pink);border-left:none;border-radius:0 37px 37px 0}
  .grafik-copy{font-size:11px;line-height:12.5px;color:var(--soft)}
  .grafik-word{font-family:var(--display);font-size:38px;line-height:40px}
  .grafik-word span{color:var(--pink);font-family:var(--sans);font-weight:600;font-size:30px;margin-right:6px}
  .section-title{font-size:28px;font-weight:300;color:var(--cyan-text)}
  .section-title b{font-weight:600;color:var(--white)}
  .service{position:absolute;top:100px;width:114px;height:140px;border-radius:0 0 57px 57px;
      background:linear-gradient(180deg, rgba(120,40,160,0) 0%, rgba(150,50,190,.55) 60%, #9a3ec4 100%);padding:10px 0 0 22px}
  .service h3{font-size:12px;line-height:13px;font-weight:600;color:var(--cyan-text);margin-bottom:12px}
  .service p{font-size:9px;line-height:10.5px;color:var(--white);padding-right:8px}
  .why{font-size:24px;line-height:25px;font-weight:700}
  .why span{color:var(--magenta);font-weight:400}
  .reasons{list-style:none;left:725px;top:270px;width:335px}
  .reasons li{display:flex;gap:12px;align-items:center;height:47px;border-bottom:1px dashed rgba(255,255,255,.25)}
  .reasons li:last-child{border-bottom:none}
  .reasons h4{font-size:12.5px;font-weight:600;color:var(--pink);line-height:14px}
  .reasons p{font-size:10px;line-height:12px;color:var(--soft)}
</style>
</head>
<body>

<section class="spread spread--outside" aria-label="Außenseite">
  <svg class="wave" viewBox="0 0 1100 555" aria-hidden="true">
    <path d="M0,270 C120,236 250,218 360,252 C470,288 540,410 640,440 C740,470 820,460 900,460 C1000,460 1060,445 1100,405 L1100,555 L0,555Z" fill="#ffffff"/>
    <path d="M0,288 C120,252 250,236 360,270 C470,306 540,428 640,458 C740,488 820,480 900,480 C1000,480 1060,466 1100,430 L1100,555 L0,555Z" fill="#93ebe6"/>
  </svg>

  <div class="abs brand-light" style="left:45px;top:38px">Tallow</div>
  <div class="abs brand-bold" style="left:45px;top:72px">Brisko</div>
  <div class="abs tagline" style="left:45px;top:112px">DESIGNS, DIE WIRKEN</div>
  <div class="abs subline" style="left:45px;top:138px">Marken, die bleiben</div>
  <div class="art art--line" style="left:372px;top:22px;width:85px;height:110px" role="img" aria-label="Linienzeichnung eines Bleistifts"></div>
  <div class="art art--line" style="left:45px;top:185px;width:185px;height:95px" role="img" aria-label="Linienzeichnungen von Stift, Zeichenfeder und Werkzeugen"></div>
  <div class="art art--line-cyan" style="left:340px;top:195px;width:70px;height:45px" role="img" aria-label="Kleine Pinselstrich-Grafik"></div>

  <div class="abs contact-pill">Kontaktiere uns für eine</div>
  <div class="abs offer-title" style="left:33px;top:348px">Kostenlose<br>Beratung!</div>
  <ul class="abs contact-list" style="left:35px;top:418px">
    <li><svg width="9" height="11" viewBox="0 0 9 11"><path d="M4.5 0C2 0 0 2 0 4.4 0 7.5 4.5 11 4.5 11S9 7.5 9 4.4C9 2 7 0 4.5 0Zm0 6a1.6 1.6 0 1 1 0-3.2 1.6 1.6 0 0 1 0 3.2Z" fill="#cf4cf2"/></svg><span>Lindenweg 42<br>60311 Frankfurt</span></li>
    <li><svg width="9" height="9" viewBox="0 0 10 10"><path d="M2 0l2 2.4-1.2 1.3c.7 1.5 1.9 2.7 3.4 3.4L7.5 6 10 8l-1.2 1.8C4.6 10 0 5.4.2 1.2Z" fill="#cf4cf2"/></svg><span>+49 123 98765</span></li>
    <li><svg width="9" height="7" viewBox="0 0 10 7"><rect width="10" height="7" rx="1" fill="#cf4cf2"/><path d="M0 .5l5 3.5 5-3.5" stroke="#fff" stroke-width=".8" fill="none"/></svg><span>hallo@tallowbrisko.de</span></li>
  </ul>
  <div class="abs url" style="left:35px;top:500px">www.<b>tallowbrisko</b>.de</div>

  <div class="abs wordmark wordmark--deep" style="left:357px;top:355px">Tallow<br>Brisko</div>
  <div class="abs owner-label" style="left:357px;top:456px">INHABER</div>
  <div class="abs owner-names" style="left:357px;top:476px">Jana Ostrow &amp;<br>Felix Brandt</div>
  <div class="art art--line" style="left:585px;top:345px;width:80px;height:115px" role="img" aria-label="Linienzeichnung einer Staffelei mit Zeichnungen"></div>

  <div class="abs hero-kicker" style="left:592px;top:40px">Dein<br>Unternehmen.<br><b>Dein Stil.</b></div>
  <div class="abs hero-title" style="left:590px;top:122px">Unser<br>Design</div>
  <div class="art art--hero" style="left:770px;top:110px;width:290px;height:300px" role="img" aria-label="Isometrische Illustration eines Bildschirms mit Grafiktablett und Farbmustern"></div>
  <div class="art art--line" style="left:845px;top:20px;width:55px;height:45px" role="img" aria-label="Linienzeichnung einer Zeichenfeder"></div>
  <div class="abs wordmark wordmark--cyan" style="left:960px;top:36px">Tallow<br>Brisko</div>
  <div class="art art--line" style="left:1020px;top:415px;width:55px;height:60px" role="img" aria-label="Linienzeichnung eines Tintenfasses mit Feder"></div>
  <div class="abs url" style="left:590px;top:500px">www.<b>tallowbrisko</b>.de</div>
</section>

<section class="spread spread--inside" aria-label="Innenseite">
  <svg class="wave" viewBox="0 0 1100 555" aria-hidden="true">
    <path d="M0,458 C150,428 300,478 450,460 C600,442 700,458 800,448 C950,432 1050,425 1100,365 L1100,555 L0,555Z" fill="#ffffff"/>
    <path d="M0,476 C150,446 300,494 450,478 C600,462 700,478 800,468 C950,454 1050,446 1100,390 L1100,555 L0,555Z" fill="#93ebe6"/>
  </svg>

  <div class="abs motto" style="left:42px;top:48px">MODERN<span>|</span>MUTIG<span>|</span>MARKANT</div>
  <div class="abs brand2-bold" style="left:42px;top:78px">Tallow</div>
  <div class="abs brand2-light" style="left:42px;top:105px">Brisko</div>
  <div class="abs rule-v" style="left:180px;top:90px;height:38px"></div>
  <div class="abs intro" style="left:203px;top:86px">gestaltet die<br>Zukunft deines<br>Unternehmensauftritts</div>
  <div class="art art--line-cyan" style="left:418px;top:40px;width:58px;height:88px" role="img" aria-label="Linienzeichnung eines Stiftehalters"></div>

  <div class="abs grafik-pill"></div>
  <div class="abs grafik-copy" style="left:44px;top:170px">Wir machen aus Ideen<br>visuelle Erlebnisse und<br>sorgen dafür, dass deine<br>Marke im Gedächtnis bleibt</div>
  <div class="abs grafik-word" style="left:212px;top:170px"><span>+</span>Grafiken</div>
  <svg class="abs" style="left:432px;top:172px" width="42" height="40" viewBox="0 0 42 40" aria-hidden="true">
    <circle cx="26" cy="20" r="13" fill="none" stroke="#ff3f6f" stroke-width="1"/>
    <path d="M0 20h14M20 14l8 6-8 6z" fill="none" stroke="#ff3f6f" stroke-width="1"/>
  </svg>
  <div class="art art--desk" style="left:40px;top:245px;width:440px;height:185px" role="img" aria-label="Illustration eines Arbeitsplatzes mit Bildschirm, Glühbirne, Farbfächer und Zeichenwerkzeugen"></div>
  <div class="art art--line" style="left:580px;top:385px;width:75px;height:70px" role="img" aria-label="Linienzeichnung einer Farbpalette"></div>

  <div class="abs section-title" style="left:578px;top:38px">Unsere <b>Leistungen</b></div>
  <div class="art art--line" style="left:945px;top:0px;width:120px;height:50px" role="img" aria-label="Linienzeichnungen von Zeichenwerkzeugen"></div>

  <article class="service" style="left:580px"><h3>Next-Level<br>Flyer</h3><p>Nicht nur Papier, sondern deine Botschaft im perfekten Look.</p></article>
  <article class="service" style="left:705px"><h3>Corporate<br>Identity</h3><p>Ein Design, das deine Marke spricht – individuell, stark, unvergesslich.</p></article>
  <article class="service" style="left:830px"><h3>Digital &amp;<br>Print</h3><p>Ob Social Media Grafiken oder klassisches Printdesign – wir sind da, wo du uns brauchst.</p></article>
  <article class="service" style="left:955px"><h3>Alles aus<br>einer Hand</h3><p>Logo, Farben, Typografie, Flyer und vieles mehr – wir bauen das Fundament für deinen Erfolg</p></article>

  <div class="abs why" style="left:579px;top:300px">Warum<br><span>wir?</span></div>
  <div class="abs rule-v" style="left:698px;top:272px;height:118px"></div>
  <ul class="abs reasons">
    <li><svg width="24" height="24" viewBox="0 0 24 24" aria-hidden="true"><circle cx="12" cy="12" r="10" fill="none" stroke="#63dde0" stroke-width="1.4"/><path d="M7 12l3.5 3.5L17 9" fill="none" stroke="#63dde0" stroke-width="1.4"/></svg><div><h4>Dein Style, unser Know-how</h4><p>Wir kombinieren deine Vision mit moderner Ästhetik.</p></div></li>
    <li><svg width="24" height="24" viewBox="0 0 24 24" aria-hidden="true"><circle cx="12" cy="12" r="10" fill="none" stroke="#63dde0" stroke-width="1.4"/><circle cx="12" cy="10" r="3" fill="none" stroke="#63dde0" stroke-width="1.4"/><path d="M6.5 18c1.5-3 9.5-3 11 0" fill="none" stroke="#63dde0" stroke-width="1.4"/></svg><div><h4>Persönlicher Service</h4><p>Wir hören zu und setzen um, was dich einzigartig macht</p></div></li>
    <li><svg width="24" height="24" viewBox="0 0 24 24" aria-hidden="true"><rect x="2" y="2" width="20" height="20" rx="3" fill="none" stroke="#63dde0" stroke-width="1.4"/><circle cx="12" cy="12" r="5" fill="none" stroke="#63dde0" stroke-width="1.4"/></svg><div><h4>Flexible Lösungen</h4><p>für die unterschiedlichsten Anforderungen</p></div></li>
  </ul>

  <div class="abs url" style="left:158px;top:500px">www.<b>tallowbrisko</b>.de</div>
  <div class="abs url" style="left:730px;top:500px">www.<b>tallowbrisko</b>.de</div>
</section>

</body>
</html>
```